Upstart Retirement Planning Firm needs help with business card design

Harborview Nest Advisors, LLC is looking for help with business card design. We give advice on investments, insurance, and other financial matters related to retirement. There are some required disclosures that we will provide but mostly we are looking for a professional, classy business card that reflects the theme we have chosen. We have a logo that is attached but we would like to add a phrase; "Turning Your Earned Income Into Retirement Income"

Doubled sided only so that we can add the required disclosures (needed for our industry) on the back of the card. We will provide the exact words for this in 1-2 days.

Target Market(s)

Retirees and Pre-retirees. Professionals 50+ years old

Industry/Entity Type

Financial Planning

Contact Information for Business Card

We currently have two people who will need separate cards so we'd like to have a template so that we can add names for new cards in the future.

For the first run, please show the following information.

Gregor Pelham, MBA, ChFC®, CLU®
Financial Advisor, Registered Representative
gpelham@harborviewnest.example
Phone: (555) 318-2946
Toll Free Fax: (800) 555-0193

Address is
2187 Meadowlark Ridge Rd.
Suite K418
Virginia Beach, VA 23999

Colors
3277b5

Requirements
Must have
• Logo, contact info, small phase to describe business (in description), required legal disclosures on back of the card as follows (in small font)
• Gregor Pelham is a registered representative of and offers securities through Brightmoor Capital Brokerage Corporation, Member FNQX. Brightmoor Capital Brokerage Corporation is a member of the Brightmoor Capital Alliance which is the marketing name for Brightmoor Holding Corporation and its affiliates.
Nice to have
• Rounded edges, raised letters
Should not have
• any colors that aren't in the logo (other than black for font)

```html
<!DOCTYPE html>
<html lang="en">
<head>
<meta charset="utf-8">
<title>Harborview Nest Advisors – Business Card</title>
<link rel="stylesheet" href="https://fonts.googleapis.com/css2?family=PT+Sans:wght@400;700&display=swap">
<style>
  :root {
    --stage: #000000;
    --card: #ffffff;
    --brand-blue: #2d56a0;
    --ink: #1a1a1a;
    --logo-gray: #5d5f63;
    --tint-blue: #e9edf5;
    --tint-soft: #f4f6fa;
    --rule: #8a8c90;
  }
  * { box-sizing: border-box; margin: 0; padding: 0; }
  html, body {
    width: 1200px; height: 900px; overflow: hidden;
    background: var(--stage);
    font-family: "PT Sans", "Myriad Pro", Arial, sans-serif;
  }
  .canvas { position: relative; width: 1200px; height: 900px; }
  .card {
    position: absolute; top: 271px;
    width: 457px; height: 281px;
    background: var(--card);
    border-radius: 14px;
    overflow: hidden;
  }
  .card--front { left: 137px; }
  .card--back { left: 626px; }

  .front-decoration {
    position: absolute; left: 0; top: 0; width: 190px; height: 200px;
    background: radial-gradient(ellipse at 30% 20%, var(--tint-blue) 0%, var(--tint-soft) 55%, rgba(255,255,255,0) 80%);
  }
  .contact {
    position: absolute; left: 191px; top: 20px;
    color: var(--ink);
  }
  .contact__name {
    font-size: 17px; font-weight: 700; color: var(--brand-blue); line-height: 20px;
  }
  .contact__credentials { font-size: 12px; }
  .contact__title { font-size: 13px; line-height: 18px; }
  .contact__list { list-style: none; margin-top: 13px; font-size: 13px; }
  .contact__list li { display: flex; align-items: center; height: 20px; }
  .contact__icon { width: 9px; height: 9px; margin: 0 6px 0 3px; fill: var(--brand-blue); }
  .contact__fax { margin-left: 3px; }
  .contact__fax-label { color: var(--brand-blue); font-weight: 700; }
  .contact__fax-number { font-weight: 700; }
  .contact__address { margin-top: 12px; font-size: 13px; line-height: 19px; }

  .brand-name {
    position: absolute; left: 18px; top: 190px; width: 165px;
    color: var(--logo-gray); font-size: 15px; font-weight: 700;
    line-height: 19px; letter-spacing: 0.3px;
  }

  .back-pattern {
    position: absolute; inset: 0;
    background: linear-gradient(180deg, var(--tint-blue) 0%, var(--tint-soft) 70%, var(--card) 100%);
  }
  .back-brand {
    position: absolute; right: 24px; top: 243px;
    color: var(--logo-gray); font-size: 14px; font-weight: 700; letter-spacing: 0.5px;
    padding-bottom: 3px; border-bottom: 1px solid var(--rule);
  }
</style>
</head>
<body>
<main class="canvas">
  <section class="card card--front" aria-label="Business card front">
    <div class="front-decoration" role="img" aria-label="Faint brand decoration"></div>
    <div class="contact">
      <p class="contact__name">Gregor Pelham, MBA<span class="contact__credentials">, ChFC®, CLU®</span></p>
      <p class="contact__title">Financial Advisor, Registered Representative</p>
      <ul class="contact__list">
        <li>
          <svg class="contact__icon" viewBox="0 0 10 10" aria-hidden="true"><path d="M2 0.5 L3.6 2.6 L2.7 3.7 Q3.8 6 6.3 7.3 L7.4 6.4 L9.5 8 L8.4 9.5 Q4.5 9.3 1.6 5.8 Q0.3 3.8 0.6 1.6 Z"/></svg>
          (555) 318-2946
        </li>
        <li>
          <svg class="contact__icon" viewBox="0 0 10 8" aria-hidden="true"><path d="M0 0 H10 V8 H0 Z M0.8 0.8 L5 4.2 L9.2 0.8 Z" fill-rule="evenodd"/></svg>
          gpelham@harborviewnest.example
        </li>
        <li class="contact__fax"><span class="contact__fax-label">Toll Free Fax:</span>&nbsp;<span class="contact__fax-number">(800) 555-0193</span></li>
      </ul>
      <p class="contact__address">2187 Meadowlark Ridge Rd. Suite<br>K418 Virginia Beach, VA 23999</p>
    </div>
    <p class="brand-name">Harborview Nest Advisors, LLC</p>
  </section>

  <section class="card card--back" aria-label="Business card back">
    <div class="back-pattern" role="img" aria-label="Faint repeating brand pattern"></div>
    <p class="back-brand">Harborview Nest Advisors, LLC</p>
  </section>
</main>
</body>
</html>
```